2018 Desk Calendar Design with Better Spine, Better Health with Chiropractic

In conjunction with the Federation of Spinal Wellness Malaysia (FSW), we are organizing a 2018 desk calendar design. The cover page and monthly design size is 210mm (H) x 195mm (W). The will be a total of 27 designs including a cover page (front) [Sample 1], cover page (back) Malaysia National & States Holiday 2018 (https://restdaylist.example.my/2018-dates/) [Sample 2], 12 months design (front) [Sample 3 and 4], 12 months design (back) [Sample 5], Last page (2017 and 2019 calendar) [Sample 6].

Below are some recommendations for monthly back cover design. The main theme remain as Better SPINE, Better HEALTH with CHIROPRACTIC. Each month can in collaborate with of the following element:-

Suggestion 1 (Celebration of the Month)
January - New Year
February - Chinese New Year
March -
April -
May - Labour Day
June - Aidilfitri Festival
July-
August - Independent Day
September - Malaysia Day
October - World Spine Day
November - Deepavali Festival
December - Christmas

Suggestion 2 (States in Malaysia)
January - Perlis
February - Kedah
March - Penang
April - Perak
May - Selangor
June - Negeri Sembilan
July- Melaka
August - Johor
September - Pahang
October - Terengganu
November - Kelantan
December - Sabah & Sarawak

Target Market(s)

Chiropractors and Public

Industry/Entity Type

Chiropractor

Colors

Designer to choose colors to be used in the design.

Requirements
Must have
• The theme for the desk calendar design is Better Spine, Better Health with Chiropractic.
• The cover page should include 5th Anniversary element.
Nice to have
• Lunar or Islamic calendar is optional in the Gregorian calendar.
• AI Format
• Footnote of each page www.spinefsw.example.org

```html
<!DOCTYPE html>
<html lang="en">
<head>
<meta charset="utf-8">
<title>Better Spine Better Health – 2018 Calendar Cover</title>
<link rel="stylesheet" href="https://fonts.googleapis.com/css2?family=Arimo:wght@400;700&display=swap">
<style>
  :root {
    --paper: #ffffff;
    --violet: #5a4ea6;
    --violet-deep: #3f3589;
    --sun: #ffe100;
    --snow: #ffffff;
    --ink: #111111;
    --photo-clinic: linear-gradient(100deg, #b7c2cc 0%, #8a9bb0 30%, #3f8fc4 55%, #5aa8d6 72%, #2b2f36 86%, #eef1f3 100%);
    --photo-consult: linear-gradient(100deg, #dcd6cf 0%, #f3f1ee 38%, #e3c7b6 55%, #5a4036 72%, #efe6df 85%, #d9c4b4 100%);
    --photo-rest: linear-gradient(100deg, #aeb98f 0%, #d4cbb8 30%, #f5f3ef 55%, #e6d6c9 72%, #f7f5f2 88%, #cdbba9 100%);
  }
  * { margin: 0; padding: 0; box-sizing: border-box; }
  html, body { width: 1200px; height: 1115px; overflow: hidden; background: var(--paper); }
  .cover {
    position: relative; width: 1200px; height: 1115px; overflow: hidden;
    background: var(--paper);
    font-family: "Arimo", Arial, sans-serif;
  }
  .photo { position: absolute; left: 0; width: 1200px; }
  .photo--treatment { top: 0; height: 360px; background: var(--photo-clinic); }
  .photo--consult { top: 372px; height: 363px; background: var(--photo-consult); }
  .photo--rest { top: 750px; height: 365px; background: var(--photo-rest); }

  .ribbons { position: absolute; inset: 0; }

  .binding {
    position: absolute; top: 8px; left: 140px; right: 0; height: 26px;
    display: flex; gap: 14px;
  }
  .binding span { width: 26px; height: 26px; background: var(--ink); flex: none; }

  .text { position: absolute; white-space: nowrap; font-weight: 700; line-height: 1; }
  .headline { color: var(--sun); font-size: 52px; }
  .headline--spine { left: 40px; top: 60px; }
  .headline--health { left: 110px; top: 138px; }
  .headline--with { left: 110px; top: 222px; font-size: 40px; }
  .rule { position: absolute; height: 4px; background: var(--snow); }
  .rule--health { left: 70px; top: 196px; width: 240px; }
  .rule--with { left: 60px; top: 274px; width: 300px; }
  .year { left: 160px; top: 290px; font-size: 122px; color: var(--snow); }
  .year-label { left: 166px; top: 410px; font-size: 58px; font-weight: 400; color: var(--sun); }

  .org-mark {
    position: absolute; left: 200px; top: 522px;
    display: flex; align-items: center; gap: 10px;
  }
  .org-mark i { width: 34px; height: 34px; border-radius: 50%; background: var(--sun); }
  .org-mark b { font-size: 44px; color: var(--sun); }

  .anniv-num { left: 12px; top: 745px; font-size: 250px; color: var(--sun); }
  .anniv-th { left: 160px; top: 830px; font-size: 44px; color: var(--sun); }
  .anniv-line1 { left: 172px; top: 900px; font-size: 46px; color: var(--sun); }
  .anniv-line2 { left: 172px; top: 955px; font-size: 46px; color: var(--sun); }
  .site { left: 20px; top: 1026px; font-size: 34px; color: var(--snow); }
</style>
</head>
<body>
<main class="cover">
  <div class="photo photo--treatment" role="img" aria-label="Photo of a chiropractor adjusting a patient's shoulder on a treatment table"></div>
  <div class="photo photo--consult" role="img" aria-label="Photo of a doctor with a stethoscope consulting a patient"></div>
  <div class="photo photo--rest" role="img" aria-label="Photo of a relaxed woman lying on her side receiving a spinal adjustment"></div>

  <svg class="ribbons" width="1200" height="1115" viewBox="0 0 1200 1115" aria-hidden="true">
    <polygon points="0,0 745,0 290,655 0,655" fill="var(--violet)" opacity="0.92"/>
    <polygon points="0,0 420,0 200,470 0,470" fill="var(--violet-deep)" opacity="0.35"/>
    <path d="M0,610 L300,640 Q330,900 475,1115 L0,1115 Z" fill="var(--violet)" opacity="0.94"/>
    <path d="M0,760 L180,700 Q240,930 300,1115 L0,1115 Z" fill="var(--violet-deep)" opacity="0.35"/>
  </svg>

  <div class="binding" aria-hidden="true">
    <span></span><span></span><span></span><span></span><span></span><span></span><span></span><span></span><span></span><span></span><span></span><span></span><span></span><span></span><span></span><span></span><span></span><span></span><span></span><span></span><span></span><span></span><span></span><span></span><span></span><span></span>
  </div>

  <h1>
    <span class="text headline headline--spine">Better SPINE</span>
    <span class="text headline headline--health">Better HEALTH</span>
    <span class="text headline headline--with">with CHIROPRACTIC</span>
  </h1>
  <div class="rule rule--health"></div>
  <div class="rule rule--with"></div>

  <p class="text year">2018</p>
  <p class="text year-label">Calendar</p>

  <div class="org-mark"><i></i><b>FSW</b></div>

  <p class="text anniv-num">5</p>
  <p class="text anniv-th">th</p>
  <p class="text anniv-line1">Celebrating</p>
  <p class="text anniv-line2">Anniversary</p>

  <p class="text site">www.spinefsw.example.org</p>
</main>
</body>
</html>
```